Business Card Design - Amberfield Court

We are looking at a new design for our business cards that has a modern and professional look. We run a residential aged care facility focussing on the care of residents. The cards will be used for potential clients, consultants and business opportunities in this sector. Blue and white is our main colours and would to see these colours incorporated in the design.
Industry/Entity Type
Business
Contact Information for Business Card
Amberfield Court, Darren Walsh, dwalsh@amberfieldcourt.com.au, Finance Manager, 0472 639 208, BCom, 37 Marrabel Crescent, Brindle Vale, Qld 4093.
Look and feel
Each slider illustrates characteristics of the customer's brand and the style your logo design should communicate.

```html
<!DOCTYPE html>
<html lang="en">
<head>
<meta charset="utf-8">
<title>Amberfield Court – Business Card</title>
<link rel="stylesheet" href="https://fonts.googleapis.com/css2?family=Open+Sans:wght@400;600&display=swap">
<style>
  :root {
    --stage: #e9e7e3;
    --card-white: #ffffff;
    --card-grey: #dcdcdc;
    --brand-blue: #3f6f86;
    --brand-blue-light: #6f9bb0;
    --band-taupe: #9c8f88;
    --ink-dark: #3a3a3a;
    --ink-mid: #555555;
  }
  * { box-sizing: border-box; margin: 0; padding: 0; }
  html, body {
    width: 1200px; height: 950px; overflow: hidden;
    background: var(--stage);
    font-family: "Open Sans", Arial, sans-serif;
  }
  .stage {
    width: 1200px; height: 950px;
    display: flex; flex-direction: column; align-items: center; justify-content: center;
    gap: 40px;
  }
  .card {
    position: relative;
    width: 700px; height: 428px;
    background: var(--card-white);
    box-shadow: 0 6px 18px rgba(0,0,0,0.18);
    overflow: hidden;
  }
  .card-back {
    background: linear-gradient(135deg, #f7f7f7 0%, var(--card-grey) 100%);
  }
  .card-art { position: absolute; inset: 0; }

  /* Front */
  .brand-lockup {
    position: absolute; left: 44px; top: 118px;
    display: flex; align-items: center; gap: 14px;
  }
  .brand-dot {
    width: 56px; height: 56px; border-radius: 50%;
    background: var(--brand-blue);
  }
  .brand-name {
    font-size: 26px; font-weight: 600; letter-spacing: 1px;
    color: var(--brand-blue); text-transform: uppercase;
  }
  .person {
    position: absolute; right: 36px; top: 66px; text-align: right; color: #fff;
  }
  .person-name { font-size: 22px; font-weight: 600; }
  .person-name .credential { font-size: 18px; font-weight: 400; }
  .person-role { font-size: 15px; margin-top: 2px; }

  .contact-list {
    position: absolute; left: 44px; top: 262px;
    list-style: none; color: var(--ink-dark); font-size: 16px;
  }
  .contact-list li { display: flex; align-items: center; gap: 10px; height: 26px; }
  .contact-icon { width: 16px; height: 16px; flex: none; }

  .address {
    position: absolute; right: 40px; bottom: 44px;
    text-align: right; color: var(--ink-mid); font-size: 17px; line-height: 1.35;
  }

  /* Back */
  .back-mark {
    position: absolute; left: 50%; top: 70px; transform: translateX(-50%);
    width: 240px; height: 240px; border-radius: 50%;
    background: var(--brand-blue);
  }
  .back-url {
    position: absolute; left: 0; right: 0; top: 330px;
    text-align: center; font-size: 24px; color: var(--ink-dark); letter-spacing: 0.5px;
  }
</style>
</head>
<body>
<main class="stage">

  <section class="card card-front" aria-label="Business card front">
    <svg class="card-art" viewBox="0 0 700 428" width="700" height="428" aria-hidden="true">
      <defs>
        <linearGradient id="bandBlue" x1="0" y1="0" x2="1" y2="0">
          <stop offset="0" stop-color="#3f6f86"/>
          <stop offset="1" stop-color="#5f8ca3"/>
        </linearGradient>
      </defs>
      <path d="M0,0 H700 V250 C600,140 380,40 0,34 Z" fill="url(#bandBlue)"/>
      <path d="M0,44 C380,50 600,150 700,262" fill="none" stroke="var(--band-taupe)" stroke-width="10"/>
      <path d="M0,56 C380,62 600,165 700,280" fill="none" stroke="var(--brand-blue-light)" stroke-width="3"/>
    </svg>

    <div class="brand-lockup">
      <span class="brand-dot"></span>
      <span class="brand-name">Amberfield Court</span>
    </div>

    <div class="person">
      <p class="person-name">Darren Walsh <span class="credential">BCom</span></p>
      <p class="person-role">Finance Manager</p>
    </div>

    <ul class="contact-list">
      <li>
        <svg class="contact-icon" viewBox="0 0 16 16"><path d="M3 1 L6 1 L7 5 L5 6 C6 8 8 10 10 11 L11 9 L15 10 L15 13 C15 14 14 15 13 15 C6 14 2 10 1 3 C1 2 2 1 3 1 Z" fill="var(--brand-blue)"/></svg>
        <span>0472 639 208</span>
      </li>
      <li>
        <svg class="contact-icon" viewBox="0 0 16 16"><rect x="1" y="3" width="14" height="10" fill="var(--brand-blue)"/><path d="M1 3 L8 9 L15 3" fill="none" stroke="#fff" stroke-width="1.4"/></svg>
        <span>dwalsh@amberfieldcourt.com.au</span>
      </li>
      <li>
        <svg class="contact-icon" viewBox="0 0 16 16"><circle cx="8" cy="8" r="7" fill="var(--brand-blue)"/><path d="M1 8 H15 M8 1 C4 5 4 11 8 15 M8 1 C12 5 12 11 8 15" fill="none" stroke="#fff" stroke-width="1"/></svg>
        <span>www.amberfieldcourt.com.au</span>
      </li>
    </ul>

    <p class="address">37 Marrabel Crescent<br>Brindle Vale, Qld 4093.</p>
  </section>

  <section class="card card-back" aria-label="Business card back">
    <div class="back-mark" role="img" aria-label="Brand emblem area"></div>
    <p class="back-url">amberfieldcourt.com.au</p>
  </section>

</main>
</body>
</html>
```